Elegant Business Card for Technology Company

Client is a supplier of innovative industrial communications and automation equipment since 2002. This contest is to gather fresh ideas for a redesign of the existing business card. Client is looking for design that best communicates tagline "Industrial Networking and Computing Specialist".

Design submissions should look modern, clean, elegant and professional. It should not be cluttered. Use white as the primary colour. Orange and black as secondary colour. Refer to jpeg File 1 on the current design.

Fonts used by Client used include Arial Regular, Arial Black, Roboto Regular, Roboto Black and Lato.

The winning design will be sent for offset printing using super white 250gsm artcard paper (open for suggestions).

Target Market(s)

System Engineers, Project Managers, Purchasing Managers from companies providing engineering services for Smart Cities.

Industry/Entity Type

Information Technology

Contact Information for Business Card

Refer to PDF File 3 for Business Card Details. Priority of short contact information would be as follows Name > Job Title > Email > Mobile > Web > Tel > Fax > Business Address >UEN (UEN represents company registration number)

Font styles to use
Sans Serif

Colors
ffffff
f37122
000000
5c5c5c

Requirements
Must have
• Refer to AI File 2 (Company Logo) & PDF File 3 (Information on Namecard)
Should not have
• No QR codes
• No Social Media Icons
• Do not create full Black or Orange colour background

```html
<!DOCTYPE html>
<html lang="en">
<head>
<meta charset="utf-8">
<title>KVR Business Card</title>
<link rel="stylesheet" href="https://fonts.googleapis.com/css2?family=Roboto:wght@400;500;900&display=swap">
<style>
  :root {
    --white: #ffffff;
    --orange: #f37122;
    --orange-deep: #e8661a;
    --black: #000000;
    --ink: #161616;
    --grey: #5c5c5c;
    --backdrop: #ece9e4;
  }
  * { margin: 0; padding: 0; box-sizing: border-box; }
  html, body { width: 1200px; height: 950px; overflow: hidden; }
  body {
    background: var(--backdrop);
    font-family: "Roboto", Arial, sans-serif;
    position: relative;
  }
  .card {
    position: absolute;
    width: 620px;
    height: 354px;
    border-radius: 20px;
    overflow: hidden;
    box-shadow: 0 10px 28px rgba(0,0,0,0.18);
  }

  /* Front: white tagline card with orange edge bands */
  .card-front {
    left: 90px; top: 80px;
    background: var(--white);
    text-align: center;
    color: var(--ink);
  }
  .front-band-top {
    position: absolute; left: 0; right: 0; top: 0;
    height: 12px;
    background: var(--orange);
  }
  .front-band-bottom {
    position: absolute; left: 0; right: 0; bottom: 0;
    height: 44px;
    background: linear-gradient(90deg, var(--orange) 0%, var(--orange-deep) 100%);
  }
  .front-brand {
    margin-top: 52px;
    font-weight: 900;
    font-size: 100px;
    line-height: 1;
    letter-spacing: -2px;
    color: var(--ink);
  }
  .front-tagline {
    margin-top: 22px;
    font-size: 17px;
    line-height: 1.3;
    font-weight: 400;
    color: var(--grey);
  }
  .front-tagline strong {
    font-weight: 500;
    color: var(--orange);
  }

  /* Back: contact card */
  .card-back {
    left: 490px; top: 500px;
    background: var(--white);
  }
  .card-back svg.wave { position: absolute; inset: 0; }
  .back-brand {
    position: absolute;
    left: 34px; top: 88px;
    display: flex; align-items: center; gap: 14px;
  }
  .brand-dot {
    width: 62px; height: 62px;
    border-radius: 50%;
    background: var(--orange);
  }
  .brand-name {
    font-weight: 900;
    font-size: 72px;
    line-height: 1;
    letter-spacing: -1px;
    color: var(--ink);
  }
  .person {
    position: absolute;
    left: 96px; top: 180px;
  }
  .person-name {
    font-size: 23px;
    font-weight: 500;
    color: var(--orange);
  }
  .person-title {
    font-size: 16px;
    color: var(--grey);
    margin-top: 2px;
  }
  .contact {
    position: absolute;
    right: 28px; top: 70px;
    text-align: right;
    color: var(--white);
    font-size: 15px;
    line-height: 1.5;
    list-style: none;
  }
  .address { margin-bottom: 6px; }
  .contact li { display: flex; justify-content: flex-end; align-items: center; gap: 8px; }
  .contact svg { width: 13px; height: 13px; flex: none; }
</style>
</head>
<body>

<section class="card card-front">
  <div class="front-band-top"></div>
  <div class="front-brand">KVR</div>
  <p class="front-tagline">
    <strong>Industrial Networking &amp; Computing Specialist</strong><br>
    Industrial Ethernet / Wireless / Cellular<br>
    Industrial &amp; Embedded Computing / Serial / Fieldbus Connectivity<br>
    IP Video Surveillance / Remote Automation
  </p>
  <div class="front-band-bottom"></div>
</section>

<section class="card card-back">
  <svg class="wave" viewBox="0 0 620 354" width="620" height="354" aria-hidden="true">
    <path fill="var(--orange)" d="M402,0 C282,48 312,205 216,258 C146,297 58,294 0,281 L0,294 C66,306 166,302 236,262 C338,204 316,44 442,0 Z"/>
    <path fill="var(--black)" d="M442,0 C316,44 338,204 236,262 C166,302 66,306 0,294 L0,354 L620,354 L620,0 Z"/>
    <path fill="none" stroke="var(--orange)" stroke-width="3" d="M0,320 C90,328 180,320 252,284 C346,234 344,70 480,0"/>
  </svg>

  <div class="back-brand">
    <span class="brand-dot"></span>
    <span class="brand-name">KVR</span>
  </div>
  <div class="person">
    <div class="person-name">Daniel Lim</div>
    <div class="person-title">Sales Manager</div>
  </div>

  <ul class="contact">
    <li class="address">28 Kallan Link<br>Brightway Hub #05-12 (Block B)<br>Singapore 419327</li>
    <li>+65 6123 4580
      <svg viewBox="0 0 16 16"><path fill="var(--orange)" d="M3 1l3 0 1 4-2 1c1 2 3 4 5 5l1-2 4 1 0 3c0 1-1 2-2 2C7 15 1 9 1 3c0-1 1-2 2-2z"/></svg>
    </li>
    <li>+65 9123 4567
      <svg viewBox="0 0 16 16"><rect x="4" y="1" width="8" height="14" rx="1.5" fill="none" stroke="var(--orange)" stroke-width="1.6"/><circle cx="8" cy="12.5" r="0.9" fill="var(--orange)"/></svg>
    </li>
    <li>+65 6123 4591
      <svg viewBox="0 0 16 16"><rect x="4" y="1" width="8" height="5" fill="var(--orange)"/><rect x="1" y="6" width="14" height="6" rx="1" fill="var(--orange)"/><rect x="4" y="10" width="8" height="5" fill="var(--orange)"/></svg>
    </li>
    <li>sales@kvr-tech.sg
      <svg viewBox="0 0 16 16"><rect x="1" y="3" width="14" height="10" rx="1" fill="var(--orange)"/><path d="M1.5 3.5L8 9l6.5-5.5" fill="none" stroke="var(--black)" stroke-width="1.4"/></svg>
    </li>
    <li>www.kvr-tech.sg
      <svg viewBox="0 0 16 16"><circle cx="8" cy="8" r="7" fill="var(--orange)"/><path d="M1 8h14M8 1c-3 4-3 10 0 14M8 1c3 4 3 10 0 14" fill="none" stroke="var(--black)" stroke-width="1.1"/></svg>
    </li>
  </ul>
</section>

</body>
</html>
```